Oil and Gas Exploration and Production company needs a business card design

We need a business card design using our logo and colors in the logo. We want a mainstream design.

```html
<!DOCTYPE html>
<html lang="en">
<head>
<meta charset="UTF-8">
<title>Solterra Oil &amp; Gas – Business Card</title>
<link rel="stylesheet" href="https://fonts.googleapis.com/css2?family=Open+Sans:wght@400;600;700&display=swap">
<style>
  :root {
    --backdrop: #2a2a2a;
    --card: #ffffff;
    --ink: #2b2724;
    --gold: #d4a12a;
    --grey: #6a6a6a;
    --shadow: rgba(0, 0, 0, 0.45);
  }
  * { margin: 0; padding: 0; box-sizing: border-box; }
  html, body {
    width: 1200px;
    height: 900px;
    overflow: hidden;
    background: var(--backdrop);
    font-family: "Open Sans", Arial, sans-serif;
  }
  .canvas {
    position: relative;
    width: 1200px;
    height: 900px;
  }
  .card {
    position: absolute;
    left: 250px;
    width: 700px;
    height: 400px;
    background: var(--card);
    box-shadow: 0 10px 30px var(--shadow);
    display: flex;
    flex-direction: column;
    align-items: center;
  }
  .card--front { top: 35px; justify-content: center; }
  .card--back { top: 465px; padding-top: 52px; }

  .brand {
    display: flex;
    align-items: center;
    gap: 16px;
  }
  .brand__dot {
    width: 38px;
    height: 38px;
    border-radius: 50%;
    background: var(--ink);
  }
  .brand__name {
    font-size: 50px;
    font-weight: 700;
    color: var(--ink);
    letter-spacing: 0.5px;
  }
  .website {
    margin-top: 70px;
    font-size: 15px;
    letter-spacing: 6px;
    color: var(--grey);
  }

  .back-mark {
    width: 100px;
    height: 100px;
    border-radius: 50%;
    background: var(--ink);
  }
  .person__name {
    margin-top: 26px;
    font-size: 22px;
    font-weight: 700;
    color: var(--ink);
    text-align: center;
  }
  .person__title {
    font-size: 15px;
    color: var(--gold);
    letter-spacing: 1px;
    text-align: center;
    margin-top: 2px;
  }
  .contact {
    margin-top: 26px;
    font-size: 15px;
    line-height: 1.5;
    color: var(--grey);
    text-align: center;
  }
  .contact b { color: var(--ink); font-weight: 700; }
</style>
</head>
<body>
<main class="canvas">
  <section class="card card--front" aria-label="Card front">
    <div class="brand">
      <span class="brand__dot"></span>
      <span class="brand__name">Solterra Oil &amp; Gas</span>
    </div>
    <p class="website">www.solterraenergy.com</p>
  </section>

  <section class="card card--back" aria-label="Card back">
    <div class="back-mark"></div>
    <h1 class="person__name">MARCUS HALE</h1>
    <p class="person__title">PRESIDENT</p>
    <address class="contact" style="font-style: normal;">
      4120 Harbor Lane Fairview, NY 11020 <b>M:</b> 555 7390 4128 <b>F:</b> 555 6402 1975<br>
      <b>P:</b> 555 2184 6031 <b>E:</b> info@solterraenergy.com
    </address>
  </section>
</main>
</body>
</html>
```